Company Mission & Values Poster

I'd like an A2 Portrait Poster displaying our company's Mission & Values.
See our website for our logo, fonts, mission & values.
https://valdintor.com.au/

Our Mission: Creating homes for abundant life
Values: Love, Thinking, Team, Zoe.

Some ideas to consider:
Mission as the Headline then
A logo for each of the 4 Values and the words

Target Market(s)

Myself & my team

Industry/Entity Type

Real Estate

Font styles to use
Other font styles liked:
• Company fonts as seen on our website

```html
<!DOCTYPE html>
<html lang="en">
<head>
<meta charset="utf-8">
<title>Valdintor — Mission &amp; Values</title>
<link rel="stylesheet" href="https://fonts.googleapis.com/css2?family=Alegreya+Sans:wght@300;400;700;800&family=Open+Sans:wght@400;700;800&display=swap">
<style>
  :root {
    --green: #0b3a2f;
    --green-soft: rgba(11, 58, 47, 0.95);
    --ink: #353535;
    --muted: #6b6b6b;
    --paper: #ffffff;
    --rule: #9aa3a0;
  }
  * { margin: 0; padding: 0; box-sizing: border-box; }
  html, body { width: 881px; height: 1200px; overflow: hidden; background: var(--paper); }
  .poster { position: relative; width: 881px; height: 1200px; background: var(--paper); overflow: hidden; font-family: "Open Sans", sans-serif; }

  .hero-photo {
    position: absolute; left: 0; top: 0; width: 881px; height: 642px;
    background: linear-gradient(180deg, #eef0f2 0%, #f3e6dc 28%, #b9c2c6 36%, #7f8f90 42%, #4f6b4a 52%, #b8aea3 62%, #d9cfc4 80%, #c4bcb2 100%);
  }

  .mission-tab {
    position: absolute; left: 493px; top: 280px; width: 353px; height: 52px;
    background: var(--paper); border-top-right-radius: 22px;
    font-weight: 800; font-size: 35px; color: var(--green);
    padding-left: 28px; line-height: 56px; letter-spacing: -0.3px;
  }
  .mission-panel {
    position: absolute; left: 493px; top: 331px; width: 353px; height: 391px;
    background: var(--green-soft); color: var(--paper);
  }
  .mission-headline {
    position: absolute; left: 28px; top: 26px;
    font-family: "Alegreya Sans", sans-serif; font-size: 50px; line-height: 58px;
  }
  .mission-headline .light { font-weight: 300; display: block; }
  .mission-headline .bold { font-weight: 800; display: block; }
  .mission-headline .rule-line { display: inline-block; width: 89px; height: 2px; background: var(--paper); vertical-align: middle; margin-left: 8px; }
  .mission-body {
    position: absolute; left: 28px; top: 273px; width: 310px;
    font-size: 12.4px; line-height: 18.4px;
  }

  .values-tab {
    position: absolute; left: 0; top: 588px; width: 352px; height: 54px;
    background: var(--green); border-top-right-radius: 24px;
    color: var(--paper); font-weight: 800; font-size: 35px; line-height: 58px;
    padding-left: 52px; letter-spacing: -0.5px;
  }

  .values-statement {
    position: absolute; left: 56px; top: 660px;
    font-family: "Alegreya Sans", sans-serif; font-weight: 700;
    font-size: 33px; line-height: 42px; color: var(--ink); white-space: nowrap;
  }

  .value { position: absolute; top: 856px; width: 150px; }
  .value-badge { display: block; width: 118px; height: 118px; }
  .value-name {
    font-family: "Alegreya Sans", sans-serif; font-weight: 700;
    font-size: 25px; line-height: 28px; color: var(--green); margin-top: 3px;
  }
  .value-text { font-size: 8px; line-height: 12px; color: var(--muted); margin-top: 3px; width: 146px; }
  .value--love { left: 53px; }
  .value--thinking { left: 269px; }
  .value--team { left: 484px; }
  .value--zoe { left: 691px; }

  .footer-rule { position: absolute; left: 0; top: 1102px; width: 881px; height: 1px; background: var(--rule); }
  .brand-name {
    position: absolute; left: 0; top: 1122px; width: 881px; text-align: center;
    font-family: "Alegreya Sans", sans-serif; font-weight: 400;
    font-size: 48px; line-height: 56px; letter-spacing: 9px; color: var(--green);
  }
</style>
</head>
<body>
<main class="poster">
  <div class="hero-photo" role="img" aria-label="Outdoor terrace with dining table and chairs among tropical plants overlooking a harbour at sunset"></div>

  <div class="mission-tab">OUR MISSION</div>
  <section class="mission-panel">
    <h1 class="mission-headline">
      <span class="light">Creating</span>
      <span class="bold">Homes For</span>
      <span class="light">Abundant</span>
      <span class="light">Life.<span class="rule-line"></span></span>
    </h1>
    <p class="mission-body">We wholeheartedly believe that home is an extraordinary place: a haven where life unfolds in all its glory. Where we find solace, make cherished memories with loved ones, and savour the natural beauty that surrounds us.</p>
  </section>

  <div class="values-tab">OUR VALUES</div>
  <h2 class="values-statement">We Believe<br>Business Can Be A<br>Force For Good. Our Values Shape The Way We<br>Work And How We Make Decisions.</h2>

  <article class="value value--love">
    <svg class="value-badge" viewBox="0 0 118 118" aria-hidden="true">
      <circle cx="59" cy="59" r="59" fill="#0b3a2f"/>
      <circle cx="59" cy="59" r="51" fill="none" stroke="#fff" stroke-width="1.5"/>
      <path d="M50 76 L32 58 A10 10 0 0 1 50 44 A10 10 0 0 1 68 58 Z" fill="#fff"/>
      <path d="M68 84 L54 70 A8 8 0 0 1 68 59 A8 8 0 0 1 82 70 Z" fill="#fff" stroke="#0b3a2f" stroke-width="3"/>
    </svg>
    <h3 class="value-name">Love</h3>
    <p class="value-text">Our mission is founded in our love and respect for people - those we develop for, those in our teams and those in the communities we create and operate within.</p>
  </article>

  <article class="value value--thinking">
    <svg class="value-badge" viewBox="0 0 118 118" aria-hidden="true">
      <circle cx="59" cy="59" r="59" fill="#0b3a2f"/>
      <circle cx="59" cy="59" r="51" fill="none" stroke="#fff" stroke-width="1.5"/>
      <g fill="none" stroke="#fff" stroke-width="3">
        <circle cx="59" cy="59" r="12"/>
        <circle cx="59" cy="59" r="4"/>
        <path d="M59 39v8M59 71v8M39 59h8M71 59h8M45 45l6 6M67 67l6 6M73 45l-6 6M51 67l-6 6"/>
      </g>
    </svg>
    <h3 class="value-name">Thinking</h3>
    <p class="value-text">We believe in the power of thinking. Our rigorous and creative processes create beautifully considered solutions for our purchasers, the communities we develop within and the environment.</p>
  </article>

  <article class="value value--team">
    <svg class="value-badge" viewBox="0 0 118 118" aria-hidden="true">
      <circle cx="59" cy="59" r="59" fill="#0b3a2f"/>
      <circle cx="59" cy="59" r="51" fill="none" stroke="#fff" stroke-width="1.5"/>
      <g fill="#fff">
        <circle cx="43" cy="44" r="6"/><circle cx="59" cy="40" r="7"/><circle cx="75" cy="44" r="6"/>
        <rect x="36" y="54" width="46" height="6" rx="3"/>
      </g>
      <path d="M40 64 A19 19 0 0 0 78 64" fill="none" stroke="#fff" stroke-width="5" stroke-dasharray="5 3"/>
    </svg>
    <h3 class="value-name">Team</h3>
    <p class="value-text">Property development is a team sport. We surround ourselves with the best designers and advisers. We strive to create an environment that allows them to do their best work and love doing it.</p>
  </article>

  <article class="value value--zoe">
    <svg class="value-badge" viewBox="0 0 118 118" aria-hidden="true">
      <circle cx="59" cy="59" r="59" fill="#0b3a2f"/>
      <circle cx="59" cy="59" r="51" fill="none" stroke="#fff" stroke-width="1.5"/>
      <g fill="none" stroke="#fff" stroke-width="3" stroke-linejoin="round">
        <path d="M36 58 L56 37 L76 58"/>
        <path d="M41 53 V82 H64"/>
        <rect x="52" y="64" width="10" height="18"/>
        <path d="M82 62 L82 84 L62 84 Z"/>
      </g>
    </svg>
    <h3 class="value-name">Zoe</h3>
    <p class="value-text">Our mission is to create places for 'Zoe' - the Greek word for abundant life. We do this through exquisite design, quality construction and celebrating nature.</p>
  </article>

  <div class="footer-rule"></div>
  <div class="brand-name">VALDINTOR</div>
</main>
</body>
</html>
```